Rebrand stationary with recently completed logo design

Need new business cards, thank you cards, letterhead, envelopes and presentation folders. The designs will be sent to a separate production firm so I need the files to be print ready.

My contact info
Reko Haliburn

Office 604-318-5047
Fax 604-371-8054

Email reko@glazemark.ca
website www.glazemark.ca

315-14720 62nd Avenue,
Langley, BC, V2K 3R8

Target Market(s)

Homeowners, businesses and contractors

Industry/Entity Type

Business

Font styles to use
Sans Serif

Colors
34a7d7

Requirements
Must have
• Like to have one side of the business card a solid color with the logo in all white. The side with all the text to be a white background
• I find the current blue on the front of the card with the white logo too dark.
Should not have
• Gradient colors

```html
<!DOCTYPE html>
<html lang="en">
<head>
<meta charset="utf-8">
<title>Glazemark Presentation Folder</title>
<link rel="stylesheet" href="https://fonts.googleapis.com/css2?family=Roboto:ital,wght@0,300;0,400;1,400&display=swap">
<style>
  :root {
    --page: #e6e7e9;
    --brand-blue: #0097d9;
    --ink: #333536;
    --muted: #6b6e70;
    --border: #8a8c8e;
    --paper: #ffffff;
  }
  html, body {
    margin: 0;
    padding: 0;
    width: 1200px;
    height: 882px;
    overflow: hidden;
    background: var(--page);
    font-family: "Roboto", "Helvetica Neue", Arial, sans-serif;
  }
  .canvas { position: relative; width: 1200px; height: 882px; }
  .folder-art { position: absolute; left: 0; top: 0; }
  .cover-title {
    position: absolute;
    left: 655px;
    top: 186px;
    margin: 0;
    font-weight: 300;
    font-size: 44px;
    line-height: 53px;
    color: var(--brand-blue);
    letter-spacing: 0.2px;
  }
  .cover-subtitle {
    position: absolute;
    left: 656px;
    top: 291px;
    margin: 0;
    font-weight: 300;
    font-size: 21px;
    color: var(--ink);
  }
  .brand-name {
    position: absolute;
    margin: 0;
    font-weight: 400;
    letter-spacing: 0.5px;
  }
  .brand-name--cover {
    left: 940px;
    top: 734px;
    font-size: 30px;
    color: var(--paper);
  }
  .brand-name--back {
    left: 110px;
    top: 766px;
    font-size: 21px;
    color: var(--brand-blue);
  }
  .contact {
    position: absolute;
    top: 771px;
    margin: 0;
    font-size: 9.5px;
    font-style: italic;
    line-height: 13px;
    color: var(--muted);
    list-style: none;
    padding: 0;
  }
  .contact li { padding-left: 11px; }
  .contact--phone { left: 255px; }
  .contact--web { left: 333px; }
  .contact--address { left: 437px; }
  .folder-label {
    position: absolute;
    left: 0;
    width: 1200px;
    top: 842px;
    text-align: center;
    font-size: 19px;
    color: var(--ink);
    margin: 0;
  }
</style>
</head>
<body>
<main class="canvas">
  <svg class="folder-art" width="1200" height="882" viewBox="0 0 1200 882" aria-hidden="true">
    <rect x="58.5" y="55.5" width="1089" height="770" fill="#fff" stroke="var(--border)" stroke-width="1"/>
    <path fill="var(--brand-blue)" d="M59,56 H603 V768 C480,745 300,722 232,645 C196,604 188,525 190,461 C160,487 110,502 59,493 Z"/>
    <path fill="var(--brand-blue)" d="M1147,493 C1096,502 1046,487 1017,461 C1019,525 1011,604 975,645 C905,722 726,745 603,768 V825 H1147 Z"/>
    <g fill="none" stroke="var(--brand-blue)" stroke-width="1">
      <path d="M257,776 q1,4 5,5 l1,-1.5 -1.5,-1.5 -1,1 q-1.5,-1 -2,-2 l1,-1 -1.5,-1.5 z"/>
      <rect x="257" y="786" width="5" height="7"/>
      <rect x="333" y="775" width="8" height="6"/>
      <path d="M333,775 l4,3 4,-3"/>
      <circle cx="337" cy="790" r="3.5"/>
      <path d="M440,779 a3,3 0 1 1 0.1,0 M440,779 l0,4"/>
    </g>
  </svg>

  <h1 class="cover-title">Protective Security<br>Window Film</h1>
  <p class="cover-subtitle">A Strong, Safe and Simple Solution</p>
  <p class="brand-name brand-name--cover">GLAZEMARK</p>
  <p class="brand-name brand-name--back">GLAZEMARK</p>

  <ul class="contact contact--phone">
    <li>604-318-5047</li>
    <li>604-371-8054</li>
  </ul>
  <ul class="contact contact--web">
    <li>reko@glazemark.ca</li>
    <li>www.glazemark.ca</li>
  </ul>
  <ul class="contact contact--address">
    <li>315-14720 62nd Avenue,</li>
    <li>Langley, BC, V2K 3R8</li>
  </ul>

  <p class="folder-label">Presentation folder</p>
</main>
</body>
</html>
```